Can You Break Boring? - Design a Dazzling Conference Program!

The 35th Annual BRQL Summit and Expo Fair is the Top-Notch event for Veterinary Technicians in Canada. With a reputation like that, the program has to knock the delegates socks off!
Are you up to the challenge?
The BRQL will provide you with the following:
-venue information (hours, floorplan etc.)
-conference logo and theme
-speaker bios and lecture abstracts (58 speakers, over 108 sessions)
-4 day agenda
-images that have been used in marketing to date
-color schemes that are preferred
We are looking for someone to take the material and create a program that is colorful, engaging and unique.
A copy of the registration brochure is attached. The winning submission will strongly resemble this document.
Updates

Project Deadline Extended
Reason: The submissions are getting closer to what we are looking for so we wish to extend the deadline to provide designers more time to submit more ideas.

Project Deadline Extended
Reason: I am looking for more concepts on the interior layout now. Please submit your ideas for: - exhibitor info pages - speaker info/lecture info pages - venue info - floorplan and agenda pages.

Target Market(s)

approx. 1200 Veterinary Technician delegates attending the conference

Industry/Entity Type

Marketing

Requirements
Must have
• - conference logo and theme (provided)
- BRQL logo (provided)
- venue floor plans
- conference schedule
- speaker bios and session abstracts
STRONG relation to the registration brochure.

```html
<!DOCTYPE html>
<html lang="en">
<head>
<meta charset="utf-8">
<title>35th Annual BRQL Summit and Expo Fair</title>
<link rel="stylesheet" href="https://fonts.googleapis.com/css2?family=Sorts+Mill+Goudy&display=swap">
<style>
  :root {
    --magenta: #a3327e;
    --purple: #6a2d8c;
    --royal: #2b4f9c;
    --cyan: #2aaac9;
    --green: #2f9b5b;
    --forest: #137a3f;
    --ink: #141414;
    --band-light: #ffffff;
    --band-mid: #ececec;
    --band-dark: #bdbdbd;
  }
  html, body {
    margin: 0;
    padding: 0;
    width: 927px;
    height: 1200px;
    overflow: hidden;
    background: #ffffff;
  }
  .cover {
    display: block;
    width: 927px;
    height: 1200px;
  }
  .band {
    fill: url(#bandShade);
    filter: drop-shadow(0 5px 6px rgba(0,0,0,0.45));
  }
  .type {
    font-family: "Sorts Mill Goudy", "Goudy Bookletter 1911", Georgia, serif;
    fill: var(--ink);
  }
  .brand-name { fill: var(--purple); font-size: 44px; }
  .brand-dot { fill: var(--green); }
  .edition { font-size: 54px; }
  .edition-sup { font-size: 30px; }
  .acronym { font-size: 300px; font-weight: 700; }
  .acr-1 { fill: var(--magenta); }
  .acr-2 { fill: var(--purple); }
  .acr-3 { fill: var(--royal); }
  .acr-4 { fill: var(--forest); }
  .event-title { font-size: 66px; }
  .venue { font-size: 34px; }
  .dates { font-size: 29px; }
  .tagline { font-size: 38px; }
</style>
</head>
<body>
<svg class="cover" viewBox="0 0 927 1200" xmlns="http://www.w3.org/2000/svg" aria-label="35th Annual BRQL Summit and Expo Fair cover">
  <defs>
    <linearGradient id="spectrum" x1="0" y1="0" x2="1" y2="0">
      <stop offset="0" stop-color="var(--magenta)"/>
      <stop offset="0.22" stop-color="var(--purple)"/>
      <stop offset="0.42" stop-color="var(--royal)"/>
      <stop offset="0.58" stop-color="var(--cyan)"/>
      <stop offset="0.74" stop-color="var(--green)"/>
      <stop offset="1" stop-color="var(--forest)"/>
    </linearGradient>
    <linearGradient id="bandShade" x1="0" y1="0" x2="0" y2="1">
      <stop offset="0" stop-color="var(--band-light)"/>
      <stop offset="0.55" stop-color="var(--band-mid)"/>
      <stop offset="1" stop-color="var(--band-dark)"/>
    </linearGradient>
  </defs>

  <rect class="backdrop" width="927" height="1200" fill="url(#spectrum)"/>

  <!-- header band -->
  <polygon class="band" points="0,0 927,0 927,92 927,200 0,222"/>
  <g class="brand">
    <circle class="brand-dot" cx="100" cy="120" r="14"/>
    <text class="type brand-name" x="124" y="135">BRQL</text>
  </g>
  <text class="type edition" x="348" y="160" transform="rotate(3 348 160)">35<tspan class="edition-sup" dy="-22">th</tspan><tspan dy="22"> Annual</tspan></text>

  <!-- acronym band -->
  <polygon class="band" points="0,268 927,205 927,458 0,540"/>
  <text class="type acronym" x="62" y="495" textLength="800" lengthAdjust="spacingAndGlyphs" transform="rotate(-4.5 62 495)"><tspan class="acr-1">B</tspan><tspan class="acr-2">R</tspan><tspan class="acr-3">Q</tspan><tspan class="acr-4">L</tspan></text>

  <!-- event title band -->
  <polygon class="band" points="0,540 927,560 927,680 0,655"/>
  <text class="type event-title" x="70" y="628" textLength="790" lengthAdjust="spacingAndGlyphs" transform="rotate(1.5 70 628)">Summit &amp; Expo Fair</text>

  <!-- venue band -->
  <polygon class="band" points="0,705 927,650 927,712 0,790"/>
  <text class="type venue" x="58" y="760" textLength="790" lengthAdjust="spacingAndGlyphs" transform="rotate(-4 58 760)">Riverside Convention Centre &amp; Grandview Hotel</text>

  <!-- dates band -->
  <polygon class="band" points="529,742 896,768 890,858 522,830"/>
  <text class="type dates" x="580" y="806" textLength="285" lengthAdjust="spacingAndGlyphs" transform="rotate(4 580 806)">February 21-23, 2013</text>

  <!-- theme -->
  <rect class="band" x="0" y="968" width="446" height="72"/>
  <text class="type tagline" x="55" y="1016">Respecting our Past.</text>
  <rect class="band" x="236" y="1052" width="442" height="72"/>
  <text class="type tagline" x="260" y="1100">Embracing our Future.</text>
</svg>
</body>
</html>
```